Yacht, Boats, Watersports company needs a redesign of business card

Hello Designers!
We are a Boat dealership company that sells fun in the water, we sell boats, Yachts, Kayaks and also yacht WaterSport toys. We are looking to redesign our business cards in to something a little bit more sophisticated. in a way that we can make better use of our company colors. I'm attaching a zipped file containing the company 3 sets of company logo which one is an horizontal another one is a vertical and also a chromed 3d logo. Also is included two set of business cards that we use and also some designs that i think it's interesting. We use PMS 2026c Orange and PMS 7687C Blue. I would like to see at least two different options with the orange as accent and also using blue as an accent color. It's really important for the business cards to have a font option and size that is legible to most people. Our current website is wwww.coralpennant.com. Please visit if you want to have a better feeling of the Boat dealership
You can send Single sided or double side options. We are now using single sided but we may be open for a double side option if we really like the design.
Target Market(s)
Marine, boat sales, yacht sales, water toys sales/
Contact Information for Business Card
Name: Dale Whitcombe
Address: 212 North Fenwick Lane,
Seabrook Cove, FL 33071
Phone: 954-731-8842
Fax: 954:731-8843
Cell: 954-382-1490
Email: dw@coralpennant.com
Website: coralpennant.com
Requirements
Must have
- the current information of the business card provided.
logo
use the PMS Colors
Nice to have
- a touch of elegance and sophistication but simple
Should not have
- should not have any typography that is hard to read, the card should be simple but yet sophisticated.

```html
<!DOCTYPE html>
<html lang="en">
<head>
<meta charset="utf-8">
<title>Coral Pennant – Business Card</title>
<link rel="stylesheet" href="https://fonts.googleapis.com/css2?family=Arimo:wght@400;700&display=swap">
<style>
  :root {
    --navy: #214884;
    --orange: #ef4f26;
    --white: #ffffff;
    --stage: #e7e9ec;
  }
  * { margin: 0; padding: 0; box-sizing: border-box; }
  html, body { width: 1200px; height: 901px; overflow: hidden; }
  body {
    background: var(--stage);
    font-family: "Arimo", Arial, sans-serif;
    display: flex;
    flex-direction: column;
    align-items: center;
    justify-content: center;
    gap: 56px;
  }
  .card {
    position: relative;
    width: 620px;
    height: 354px;
    overflow: hidden;
    box-shadow: 0 6px 18px rgba(0,0,0,0.18);
  }
  .card-back { background: var(--navy); }
  .card-front { background: var(--white); }

  .brand {
    position: absolute;
    display: flex;
    align-items: center;
    gap: 14px;
  }
  .brand-dot {
    border-radius: 50%;
    border: 5px solid currentColor;
    flex: none;
  }
  .brand-name {
    font-weight: 700;
    text-transform: uppercase;
    letter-spacing: 0.08em;
    white-space: nowrap;
  }
  .card-back .brand {
    left: 50%; top: 50%;
    transform: translate(-50%, -50%);
    color: var(--white);
  }
  .card-back .brand-dot { width: 64px; height: 64px; }
  .card-back .brand-name { font-size: 36px; }

  .card-front .brand {
    left: 36px; top: 162px;
    gap: 10px;
    color: var(--navy);
  }
  .card-front .brand-dot { width: 32px; height: 32px; border-width: 4px; }
  .card-front .brand-name { font-size: 18px; letter-spacing: 0.06em; }

  .panel { position: absolute; inset: 0; width: 620px; height: 354px; }

  .contact {
    position: absolute;
    left: 372px;
    top: 52px;
    color: var(--white);
    font-size: 13px;
    line-height: 1.35;
  }
  .person-name {
    color: var(--orange);
    font-size: 21px;
    font-weight: 700;
    text-transform: uppercase;
    letter-spacing: 0.02em;
    margin-bottom: 12px;
  }
  .address { margin-bottom: 12px; padding-left: 14px; }
  .lines { list-style: none; }
  .lines li { display: flex; align-items: center; gap: 7px; }
  .lines svg { width: 12px; height: 12px; flex: none; fill: var(--white); }
</style>
</head>
<body>

  <section class="card card-back" aria-label="Card back">
    <div class="brand">
      <span class="brand-dot"></span>
      <span class="brand-name">Coral Pennant</span>
    </div>
  </section>

  <section class="card card-front" aria-label="Card front">
    <svg class="panel" viewBox="0 0 620 354" aria-hidden="true">
      <path d="M268 0 Q276 200 392 292 Q296 196 284 0 Z" fill="var(--orange)"/>
      <path d="M296 0 Q300 282 520 354 L620 354 L620 0 Z" fill="var(--navy)"/>
    </svg>

    <div class="brand">
      <span class="brand-dot"></span>
      <span class="brand-name">Coral Pennant</span>
    </div>

    <div class="contact">
      <p class="person-name">Dale Whitcombe</p>
      <p class="address">212 North Fenwick Lane,<br>Seabrook Cove, FL 33071</p>
      <ul class="lines">
        <li><svg viewBox="0 0 12 12"><path d="M3 0h6a1 1 0 0 1 1 1v10a1 1 0 0 1-1 1H3a1 1 0 0 1-1-1V1a1 1 0 0 1 1-1zm0 2v7h6V2z"/></svg>954-731-8842</li>
        <li><svg viewBox="0 0 12 12"><path d="M2 1l2-1 2 3-1.5 1.2a6 6 0 0 0 3.3 3.3L9 6l3 2-1 2c-4 1-10-5-9-9z"/></svg>954-382-1490</li>
        <li><svg viewBox="0 0 12 12"><path d="M3 0h6v3H3zM1 4h10v5H9v3H3V9H1zm3 4v3h4V8z"/></svg>954:731-8843</li>
        <li><svg viewBox="0 0 12 12"><path d="M0 2h12v8H0zm1 1v.4l5 3.3 5-3.3V3zm0 1.6V9h10V4.6L6 8z"/></svg>dw@coralpennant.com</li>
        <li><svg viewBox="0 0 12 12"><circle cx="6" cy="6" r="5.5"/></svg>www.coralpennant.com</li>
      </ul>
    </div>
  </section>

</body>
</html>
```